Modern & Fresh Vantacor Book Cover

Need a creative e-book cover for my book.

Title: Master Vantacor Fast
Subtitle: Learn How To Easily Choose & Enroll in the Perfect Coverage at the Perfect Time.

Target Market(s)

60-70 year olds in the United States

Font styles to use
Sans Serif

Colors
9bcb3c
33a6d7

Requirements
Must have
• Must look modern and fresh.
• Use our company colors www.Movaquill.com

```html
<!DOCTYPE html>
<html lang="en">
<head>
<meta charset="utf-8">
<title>Master Vantacor Fast – Book Cover</title>
<link rel="stylesheet" href="https://fonts.googleapis.com/css2?family=Anton&family=Bebas+Neue&family=Montserrat:wght@400;700&display=swap">
<style>
  :root {
    --cover-bg: #ffffff;
    --title-blue: #2c7bbc;
    --title-green: #7dad3a;
    --rule-blue: #6aa0d0;
    --subtitle-gray: #444444;
    --art-light: #f4f5f6;
    --art-mid: #b9c0c6;
  }
  html, body {
    margin: 0;
    padding: 0;
    width: 800px;
    height: 1200px;
    overflow: hidden;
    background: var(--cover-bg);
  }
  .book-cover {
    position: relative;
    width: 800px;
    height: 1200px;
    background: var(--cover-bg);
    overflow: hidden;
  }
  .cover-title {
    position: absolute;
    left: 0;
    top: 0;
    width: 800px;
    height: 620px;
    display: block;
  }
  .title-lead { font-family: "Montserrat", sans-serif; font-weight: 700; fill: var(--title-blue); }
  .title-main { font-family: "Anton", sans-serif; fill: var(--title-green); }
  .title-accent { font-family: "Anton", sans-serif; fill: var(--title-blue); }
  .title-rule { stroke: var(--rule-blue); stroke-width: 4; }
  .cover-subtitle {
    position: absolute;
    left: 50px;
    top: 615px;
    width: 660px;
    margin: 0;
    font-family: "Montserrat", sans-serif;
    font-weight: 400;
    font-size: 22.5px;
    line-height: 30px;
    letter-spacing: 0.5px;
    text-align: center;
    color: var(--subtitle-gray);
  }
  .cover-art {
    position: absolute;
    left: 96px;
    top: 768px;
    width: 608px;
    height: 270px;
    border-radius: 8px;
    background: radial-gradient(ellipse at 50% 45%, var(--art-light) 0%, #e3e6e9 55%, var(--art-mid) 100%);
  }
  .cover-author {
    position: absolute;
    left: 0;
    top: 1110px;
    width: 800px;
    margin: 0;
    font-family: "Bebas Neue", sans-serif;
    font-size: 60px;
    line-height: 60px;
    letter-spacing: 9px;
    text-indent: 9px;
    text-align: center;
    color: var(--title-blue);
  }
</style>
</head>
<body>
  <main class="book-cover">
    <svg class="cover-title" viewBox="0 0 800 620" aria-labelledby="cover-title-text">
      <title id="cover-title-text">Master Vantacor Fast</title>
      <line class="title-rule" x1="94" y1="100" x2="196" y2="100"/>
      <line class="title-rule" x1="604" y1="100" x2="706" y2="100"/>
      <text class="title-lead" x="400" y="146" font-size="126" text-anchor="middle" textLength="380" lengthAdjust="spacingAndGlyphs">MASTER</text>
      <text class="title-main" x="81" y="307" font-size="151" textLength="636" lengthAdjust="spacingAndGlyphs">VANTACOR</text>
      <text class="title-accent" x="81" y="594" font-size="307" textLength="637" lengthAdjust="spacingAndGlyphs">FAST</text>
    </svg>

    <p class="cover-subtitle">Learn How To Easily Choose &amp; Enroll in the Perfect<br>Coverage at the Perfect Time.</p>

    <div class="cover-art" role="img" aria-label="Illustration of a stethoscope whose tubing forms a maze, casting a soft shadow"></div>

    <p class="cover-author">AUTHOR NAME</p>
  </main>
</body>
</html>
```